Maple Roster Business Card for recruitment company

We are looking for a Business Card Design that incorporates our personal details and our busines name and logo. We are a specialized search consultancy that recruit Property and Construction professionals.
We would like a business card that stands out and is appealing to the Construction and Property industry as well.

Target Market(s)

people in the construction and property industry

Contact Information for Business Card

Business Name and logo

Font styles to use
Serif

Colors
0094D4
00A9DD
6FCCEA
C7EBF8
E9F6FB

Requirements
Must have
• Business name and logo as well as contact details
Should not have
• No photos of us please

```html
<!DOCTYPE html>
<html lang="en">
<head>
<meta charset="utf-8">
<title>Maple Roster Business Card</title>
<link href="https://fonts.googleapis.com/css2?family=Lato:wght@300;400;700&display=swap" rel="stylesheet">
<style>
  :root {
    --page-bg: #e6e7e9;
    --card-white: #ffffff;
    --card-dark: #2c2d2f;
    --brand-teal: #0d5468;
    --text-grey: #8a8a8a;
    --band-grey: #8c8c8c;
    --brand-silver: #b9babc;
  }
  * { margin: 0; padding: 0; box-sizing: border-box; }
  html, body { width: 1200px; height: 929px; overflow: hidden; }
  body {
    background: var(--page-bg);
    font-family: "Lato", sans-serif;
    display: flex;
    flex-direction: column;
    align-items: center;
    justify-content: center;
    gap: 40px;
  }
  .card {
    position: relative;
    width: 700px;
    height: 400px;
    box-shadow: 0 6px 18px rgba(0,0,0,0.18);
    overflow: hidden;
  }
  .card--front { background: var(--card-white); }
  .card--back {
    background: var(--card-dark);
    display: flex;
    align-items: center;
    justify-content: center;
  }
  .brand-name {
    font-family: "Lato", sans-serif;
    font-weight: 300;
    letter-spacing: 2px;
    text-transform: uppercase;
    white-space: nowrap;
  }
  .card--front .brand-name {
    position: absolute;
    left: 46px;
    top: 178px;
    font-size: 40px;
    color: var(--brand-teal);
  }
  .card--back .brand-name {
    font-size: 60px;
    color: var(--brand-silver);
  }
  .divider {
    position: absolute;
    left: 380px;
    top: 70px;
    width: 1.5px;
    height: 260px;
    background: var(--brand-teal);
  }
  .details {
    position: absolute;
    left: 410px;
    top: 78px;
    color: var(--text-grey);
  }
  .details__name {
    font-size: 30px;
    font-weight: 400;
    color: var(--brand-teal);
    line-height: 1.05;
  }
  .details__title {
    font-size: 19px;
    margin-bottom: 16px;
  }
  .details__address {
    font-size: 17px;
    line-height: 1.3;
    margin-bottom: 6px;
  }
  .contact-list { list-style: none; }
  .contact-list li {
    display: flex;
    align-items: center;
    gap: 12px;
    font-size: 17px;
    line-height: 1.45;
  }
  .contact-list svg { width: 16px; height: 16px; fill: var(--brand-teal); flex: none; }
  .band {
    position: absolute;
    bottom: 0;
    height: 14px;
  }
  .band--teal { left: 0; width: 450px; background: var(--brand-teal); }
  .band--grey { left: 460px; right: 0; background: var(--band-grey); }
</style>
</head>
<body>
  <section class="card card--front">
    <div class="brand-name">Maple Roster</div>
    <div class="divider"></div>
    <div class="details">
      <div class="details__name">Dana Whitfield</div>
      <div class="details__title">President</div>
      <div class="details__address">012 Physical Address 000<br>United State 5551</div>
      <ul class="contact-list">
        <li>
          <svg viewBox="0 0 16 16"><path d="M3 1l3 3-1.5 2a9 9 0 0 0 5.5 5.5L12 10l3 3-2 2C7 15 1 9 1 3z"/></svg>
          012 3456 7890
        </li>
        <li>
          <svg viewBox="0 0 16 16"><path d="M4 1h8v4H4zM1 6h14v6h-3v3H4v-3H1zM5 10v4h6v-4z"/></svg>
          00000000051
        </li>
        <li>
          <svg viewBox="0 0 16 16"><path d="M1 3h14v10H1zM2 4l6 5 6-5v-0H2z" fill-rule="evenodd"/></svg>
          info@yourmail.com
        </li>
        <li>
          <svg viewBox="0 0 16 16"><path d="M8 1a7 7 0 1 0 0 14A7 7 0 0 0 8 1zm0 1.3c.9 0 1.9 1.9 2.1 4.7H5.9C6.1 4.2 7.1 2.3 8 2.3zM2.4 7h2.2c.1-1.6.4-3 .9-4A5.7 5.7 0 0 0 2.4 7zm8.9 0h2.3a5.7 5.7 0 0 0-3.2-4c.5 1 .8 2.4.9 4zM2.4 9a5.7 5.7 0 0 0 3.1 4c-.5-1-.8-2.4-.9-4zm3.5 0c.2 2.8 1.2 4.7 2.1 4.7s1.9-1.9 2.1-4.7zm5.4 0c-.1 1.6-.4 3-.9 4a5.7 5.7 0 0 0 3.2-4z"/></svg>
          www.yourwebside.com
        </li>
      </ul>
    </div>
    <div class="band band--teal"></div>
    <div class="band band--grey"></div>
  </section>

  <section class="card card--back">
    <div class="brand-name">Maple Roster</div>
  </section>
</body>
</html>
```